BrindleStaffing Business Card Design

We are a staffing company finding positions for dedicated nurses and physicians.

Target Market(s)

Business Professionals

Industry/Entity Type

Staffing

Contact Information for Business Card

Gordon Pratley
Chairman
417 39th Avenue South
SAINT PETERSBURG FL 33712
813-555-4172 Mobile
813-555-8036 Fax
gpratley@brindlestaffing.com
www.brindlestaffing.com

Font styles to use
Sans Serif

Colors
fbee3e
f04a50
f37122

Requirements
Must have
• Logo Attached, see colors below. We'd like to see Yellow, Orange and Red.

```html
<!DOCTYPE html>
<html lang="en">
<head>
<meta charset="utf-8">
<title>BrindleStaffing Business Card</title>
<link rel="stylesheet" href="https://fonts.googleapis.com/css2?family=Lato:wght@400&family=Poppins:wght@500;600&display=swap">
<style>
  :root {
    --backdrop: #2b2b2b;
    --card-white: #ffffff;
    --brand-yellow: #fbee3e;
    --brand-orange: #f37122;
    --brand-red: #f04a50;
    --ink: #1f1f1f;
    --muted: #6a6a6a;
    --rule: #c9a9a0;
    --rule-grey: #8a8a8a;
  }
  * { margin: 0; padding: 0; box-sizing: border-box; }
  html, body { width: 1200px; height: 1200px; overflow: hidden; }
  body {
    background: var(--backdrop);
    position: relative;
    font-family: "Lato", sans-serif;
  }
  .card {
    position: absolute;
    top: 310px;
    width: 364px;
    height: 594px;
    box-shadow: 0 3px 8px rgba(0,0,0,0.45);
    overflow: hidden;
  }
  .card-front { left: 234px; background: var(--card-white); }
  .card-back { left: 630px; width: 366px; }

  .wordmark {
    position: absolute;
    left: 0; right: 0;
    text-align: center;
    font-family: "Poppins", sans-serif;
    font-weight: 600;
    font-size: 33px;
    letter-spacing: -0.5px;
    white-space: nowrap;
  }
  .card-front .wordmark { top: 170px; color: var(--brand-red); }
  .card-back .wordmark { top: 280px; color: #ffffff; }

  .holder-name {
    position: absolute;
    top: 318px; left: 0; right: 0;
    text-align: center;
    font-family: "Poppins", sans-serif;
    font-weight: 500;
    font-size: 25px;
    letter-spacing: -0.3px;
  }
  .holder-name .first { color: var(--brand-orange); }
  .holder-name .last { color: var(--brand-red); }

  .holder-title {
    position: absolute;
    top: 352px; left: 0; right: 0;
    text-align: center;
    font-size: 14px;
    letter-spacing: 1.5px;
    text-transform: uppercase;
    color: var(--muted);
  }

  .icon-row {
    position: absolute;
    top: 378px; left: 86px;
  }

  .contact {
    position: absolute;
    left: 0; right: 0;
    text-align: center;
    color: var(--ink);
    font-size: 16px;
    line-height: 21px;
    white-space: nowrap;
  }
  .contact-lines { top: 412px; }
  .contact-rule {
    position: absolute;
    top: 506px; left: 87px;
    width: 196px; height: 1px;
    background: var(--rule);
  }
  .contact-address { top: 515px; }

  .back-pattern {
    position: absolute; inset: 0;
    background: linear-gradient(180deg, var(--brand-yellow) 0%, var(--brand-orange) 48%, var(--brand-red) 100%);
  }
  .back-url {
    position: absolute;
    top: 525px; left: 0; right: 0;
    text-align: center;
    color: #ffffff;
    font-size: 16.5px;
    letter-spacing: 0.6px;
  }
</style>
</head>
<body>
  <section class="card card-front">
    <div class="wordmark">BrindleStaffing</div>

    <div class="holder-name"><span class="first">Gordon</span> <span class="last">Pratley</span></div>
    <div class="holder-title">Chairman</div>

    <svg class="icon-row" width="192" height="26" viewBox="0 0 192 26" aria-hidden="true">
      <line x1="0" y1="13" x2="52" y2="13" stroke="var(--rule-grey)" stroke-width="1"/>
      <line x1="140" y1="13" x2="192" y2="13" stroke="var(--rule-grey)" stroke-width="1"/>
      <circle cx="68" cy="13" r="12" fill="var(--brand-orange)"/>
      <circle cx="96" cy="13" r="12" fill="var(--brand-orange)"/>
      <circle cx="124" cy="13" r="12" fill="var(--brand-orange)"/>
      <path d="M64.5 7.5 l2.5 -0.5 l1.5 3.5 l-1.6 1.2 q1.2 2.6 3.4 3.6 l1.2 -1.6 l3.5 1.5 l-0.5 2.5 q-1 1.3 -3 1 q-6.5 -2 -8 -8.5 q-0.3 -2 1 -2.7z" fill="#fff"/>
      <rect x="89" y="8.5" width="14" height="9" fill="none" stroke="#fff" stroke-width="1.5"/>
      <path d="M89 8.5 l7 5.5 l7 -5.5" fill="none" stroke="#fff" stroke-width="1.5"/>
      <circle cx="124" cy="13" r="6.5" fill="none" stroke="#fff" stroke-width="1.5"/>
      <ellipse cx="124" cy="13" rx="2.8" ry="6.5" fill="none" stroke="#fff" stroke-width="1.2"/>
      <line x1="117.5" y1="13" x2="130.5" y2="13" stroke="#fff" stroke-width="1.2"/>
    </svg>

    <div class="contact contact-lines">
      813-555-4172 Mobile<br>
      813-555-8036 Fax<br>
      gpratley@brindlestaffing.com<br>
      www.brindlestaffing.com
    </div>
    <div class="contact-rule"></div>
    <div class="contact contact-address">
      417 39th Avenue South<br>
      SAINT PETERSBURG FL 33712
    </div>
  </section>

  <section class="card card-back">
    <div class="back-pattern" role="img" aria-label="Soft scattered circle pattern over a yellow to orange to red gradient"></div>
    <div class="wordmark">BrindleStaffing</div>
    <div class="back-url">www.brindlestaffing.com</div>
  </section>
</body>
</html>
```